KRV Packaging design for beauty industry

Looking for my first product packaging design, tailored to reflect KRV’s branding and product benefits, along with mockup suggestions to bring it to life.

---

Front of the Box Copy
**Header**:
KRV Zenith Max Upright Dryer

**Subheader**:
Effortless Styling. Professional Results.

**Features (Use Icons + Text)**:
- **Adjustable Height**: Perfect for all users and settings.
- **Ionic Technology**: Faster drying, frizz-free results.
- **360° Heat Distribution**: Even styling every time.
- **Lightweight & Portable**: Easy to move and assemble.

**Call to Action (CTA)**:
*“Elevate Your Look with KRV Professional-Grade Tools.”*

---

### **Side Panel Copy**
**About KRV**:
"At KRV, we believe beauty is power. Our tools are designed with precision, ensuring every style feels as beautiful as you are."

**Key Benefits**:
- 3 Heat Settings for customizable control.
- Quiet operation for a professional salon experience.
- Compact foldable design for storage and travel.

**Contact Info**:
KRV Beauty | **www.KRVhome.com**
Customer Care: care@KRVhome.com

---

### **Back Panel Copy**
**Product Specifications**:
- Voltage: 110V-240V
- Adjustable Height Range: X to Y inches
- Dryer Weight: X lbs

**What’s Included**:
- 1 Stand-Up Dryer
- Adjustable Stand
- User Manual

**Care Instructions**:
"Clean with a damp cloth after use. Store in a cool, dry place."

**Certifications**:
(Include icons for UL, CE, RoHS, and recycling).

**Barcode Area**: Leave space for the UPC code.

---

### **Mockup Suggestions**
1. **Front View**:
- Use a glossy royal purple background with a clean, central placement of the KRV logo in metallic gold.
- Include a product photo or 3D render in high resolution showing the dryer in action or as a standalone image.
- Highlight features using icons with gold or white text.

2. **Side View**:
- Use a lifestyle image (e.g., a stylist using the dryer in a salon).
- Incorporate a vertical gold stripe or gradient to add luxury while separating text sections.

3. **Back View**:
- A clean layout with product details, specifications, and what's included.
- Use gold accents to frame sections for easy readability.

4. **Top Panel**:
- Simple branding with just the KRV logo and tagline: *"Kind, Radiant, Vivid."*

The competition:
https://www.brellomart.com/products/warm-glow-07314?ref=QzT81mPvLx4Wd0YhRk2NcBs7JuEa9FgVo3iXqH6yTn5KwLd

Feel free to use the phots by the "the completion" but remove logo and add KRV logo .
https://files.plovia.net/share/9Qw3LzRt7XvN2mKb5HcYp8DfJe4SaGu?mode=view_link
Size: 48x36.5x48 CM

Logo: https://files.plovia.net/share/9Qw3LzRt7XvN2mKb5HcYp8DfJe4SaGu?mode=view_link
Also im not able to attached the AI file of the logo. Please message me your email and I'll email it to you.

Thank you!
Happy designing!

Target Market(s)

Target Audience for KRV’s First Product Demographics: Age: 18-40 years old Gender: Primarily women Income Level: Middle to upper-middle income, willing to invest in quality beauty products. Geographics: Urban and suburban areas across the U.S., where beauty culture is strong and highly influenced by social media and fashion trends. Psychographics: Beauty Enthusiasts: Individuals who prioritize their appearance and enjoy experimenting with beauty products. Trendsetters: Consumers who follow the latest beauty trends, influenced by social media and influencers. Self-Expression Advocates: Those who see beauty as a form of self-care and a way to express their personality and confidence. Behavioral Characteristics: Purchase Habits: Frequently buy beauty tools and products online or in beauty supply stores. Look for high-quality, professional-grade, and aesthetically pleasing products. Product Expectations: Easy-to-use, reliable, and results-driven. Luxurious feel without an excessively high price point. Engagement: Active on social media platforms like Instagram, TikTok, and YouTube. Trust peer reviews, influencer recommendations, and user-generated content. Customer Needs: Products that simplify beauty routines. Tools and supplies that are versatile and cater to diverse beauty needs, particularly for African American women (a key segment for KRV).

Industry/Entity Type

Industry Overview Primary Industry: Beauty and Personal Care: Encompasses products and tools for hair, skin, nails, and cosmetics. Sub-Sector: Hair Care & Styling Tools: Includes professional-grade tools like dryers, flat irons, and curling wands, along with supporting products like shampoos, conditioners, and styling creams.

Font styles to use
Serif

Requirements
Must have
• Must-Haves for the Packaging Brand Identity: Prominent display of the KRV logo in metallic gold to reinforce brand recognition. Consistent use of royal purple as the background color with metallic gold and white typography for a luxurious feel. Clear Product Information: Product Name: Clearly labeled as "KRV Zenith Max Upright Dryer" on the front. Key Features: Use icons with text to highlight: Adjustable Height Ionic Technology 360° Heat Distribution Lightweight & Portable Visual Appeal: High-quality product image or 3D render showcasing the dryer. Lifestyle imagery on the side panels to show the product in use, emphasizing its professional and stylish appeal. Call to Action (CTA): Include a tagline like: “Elevate Your Look with KRV Professional-Grade Tools.” Functional Details: Product Specifications: Include voltage, dimensions, and weight on the back panel. What’s Included: Clearly list all box contents. Certifications and Compliance: Add icons for UL, CE, RoHS, and recycling to ensure credibility and eco-conscious appeal. Contact Information: Website: www.KRVhome.com Customer care email: care@KRVhome.com Barcode Area: Leave space for the UPC code on the back panel. Packaging Consistency: Uniform design elements across all panels for a cohesive look (color scheme, typography, and layout). Professional and Luxurious Finish: A glossy or matte finish with possible embossing on the logo for a premium touch.
Nice to have
• Nice-to-Have Elements Interactive Design Features: QR Code: Link to a demo video, tutorial, or assembly instructions for added customer engagement. Augmented Reality (AR): An AR feature that allows customers to see the dryer in a 360° view or visualize it in their space. Texture and Finishes: Embossed or Debossed Details: Highlight the KRV logo or key features with embossed or debossed effects for a tactile, premium feel. Spot UV Coating: Add gloss to key areas like the logo or icons to make them pop. Eco-Friendly Touch: Recyclable or biodegradable materials for the packaging. A small section emphasizing sustainability with a message like: “KRV is committed to beauty and the environment.” Unique Structural Design: Magnetic flap or window cutout to allow customers to peek at the product inside. A handle or carrying feature for easy transport, aligning with the portable nature of the dryer. Inspirational Touch: Include a short, empowering quote or message on the inside flap, such as: “Each look holds a moment—KRV lets you shape yours.” Custom Illustrations: Subtle, artistic illustrations (e.g., flowing hair, heat waves) integrated into the design background to emphasize beauty and technology. Additional Branding Elements: A tagline or hashtag like #KRVRadiance to encourage customers to share their experience on social media. Icons or badges for unique selling points, such as "Professional-Grade Quality" or "Salon Approved." Convenience Features: Printed assembly instructions or key features inside the box for ease of use. Perforated areas for easy opening. Color Gradients or Patterns: Add subtle gradients in the royal purple background for depth. Incorporate gold patterns (like geometric shapes or soft waves) for a modern touch. Seasonal or Limited-Edition Elements: A special ribbon or sticker indicating a “First Edition” or “Limited Release” to create exclusivity.
Should not have
• What the Packaging Should NOT Have Overcrowded Design: Avoid cluttering the box with too much text, small icons, or excessive design elements. A clean and elegant layout is key. Low-Quality Imagery: Do not use low-resolution product photos or stock images that don’t align with the premium look of your brand. Overused or Generic Icons: Skip overly common or generic symbols (e.g., basic checkmarks or lightning bolts). Custom, elegant icons are more appealing. Inconsistent Branding: Do not use colors, fonts, or design elements that stray from the royal purple, gold, and white branding. Consistency builds recognition. Unclear Information: Avoid vague or ambiguous descriptions. Clearly explain features, benefits, and product specifications. Cheap Materials: Packaging that feels flimsy or poorly constructed can reduce perceived value. Invest in durable materials. Overly Trendy Fonts: Avoid overly decorative or hard-to-read fonts. Stick with modern, clean typography that aligns with luxury branding. Busy Backgrounds: Don’t use loud patterns, excessive gradients, or background images that distract from key elements like the logo and product image. Misleading Claims: Avoid exaggerated or false claims (e.g., “World’s Best Dryer”) that could harm your brand’s credibility. Unnecessary Jargon: Avoid overly technical language that might confuse customers. Use simple, benefit-driven terms instead. Cliché Beauty Imagery: Skip generic, overused beauty symbols (e.g., oversized hair strands or glowing light effects) that don’t add value or originality. Lack of Contrast: Ensure text is easily readable. Avoid color combinations (like gold on light backgrounds) that reduce legibility. Lack of Accessibility: Don’t forget about inclusive design. Avoid small text or icons that are hard to read for visually impaired customers.

```html
<!DOCTYPE html>
<html lang="en">
<head>
<meta charset="utf-8">
<title>KRV Zenith Max Upright Dryer – Packaging Panels</title>
<link href="https://fonts.googleapis.com/css2?family=Playfair+Display:wght@400;600;700;800&family=Cormorant+Garamond:ital,wght@0,400;0,500;0,600;1,400&display=swap" rel="stylesheet">
<style>
  :root{
    --purple:#5a1a86;
    --purple-deep:#3e0f61;
    --purple-light:#7a2fae;
    --gold:#c9a24f;
    --gold-light:#e8cd84;
    --gold-dark:#9c7630;
    --white:#ffffff;
    --cream:#f3ead8;
    --stage:#f4f4f4;
  }
  *{box-sizing:border-box;margin:0;padding:0}
  html,body{width:1200px;height:3084px;overflow:hidden;background:var(--stage)}
  body{font-family:"Cormorant Garamond",Georgia,serif;color:var(--white)}
  .sheet{width:1200px;height:3084px;display:flex;flex-direction:column}
  .stage{height:1028px;display:flex;align-items:center;justify-content:center}

  .panel{position:relative;background:radial-gradient(ellipse at 60% 35%,var(--purple-light) 0%,var(--purple) 45%,var(--purple-deep) 100%);overflow:hidden;box-shadow:0 20px 40px rgba(40,10,60,.18)}
  .panel--face{width:900px;height:900px}
  .panel--side{width:684px;height:900px}

  .brand-tab{position:absolute;left:70px;top:0;width:150px;height:150px;background:linear-gradient(135deg,var(--gold-light),var(--gold) 50%,var(--gold-dark));display:flex;align-items:center;justify-content:center}
  .brand-tab__name{font-family:"Playfair Display",Georgia,serif;font-weight:700;font-size:52px;color:var(--purple-deep);letter-spacing:2px}

  .title{position:absolute;left:70px;top:190px;font-family:"Playfair Display",Georgia,serif;line-height:.95}
  .title__main{display:block;font-size:96px;font-weight:800;color:var(--white)}
  .title__sub{display:block;font-size:58px;font-weight:600;color:var(--gold-light);margin-top:14px}

  .product-visual{position:absolute;border-radius:50% 50% 8px 8px;background:radial-gradient(circle at 40% 30%,#f5f5f5,#b9b9c2 45%,#3a3a44 100%)}
  .product-visual--front{right:50px;top:60px;width:400px;height:520px}
  .product-visual--back{left:330px;top:360px;width:170px;height:330px;background:radial-gradient(circle at 40% 25%,#d8c0ef,#8c4fc2 40%,#4a2a6a 100%)}

  .tagline{position:absolute;font-size:22px;letter-spacing:5px;text-transform:uppercase;color:var(--gold-light);line-height:1.4}
  .tagline--front{left:0;right:0;top:610px;text-align:center}
  .tagline--back{right:60px;top:130px;text-align:left;width:330px}

  .rule{position:absolute;height:1px;background:var(--gold)}

  .features{position:absolute;left:60px;right:60px;top:690px;display:flex;justify-content:space-between}
  .feature{width:180px;text-align:center}
  .feature__icon{width:64px;height:64px;margin:0 auto 10px;border:2px solid var(--gold);border-radius:50%;display:flex;align-items:center;justify-content:center}
  .feature__label{font-size:18px;font-weight:600;color:var(--white);line-height:1.15}
  .feature__note{font-size:14px;color:var(--cream);margin-top:4px}

  .cta{position:absolute;left:70px;bottom:44px;font-size:22px;font-style:italic;color:var(--cream)}
  .cta--front{left:0;right:0;text-align:center}

  .spec-card{position:absolute;right:60px;top:260px;width:330px;border:1.5px solid var(--gold);padding:22px 24px}
  .spec-card__heading{font-family:"Playfair Display",Georgia,serif;font-size:20px;font-weight:700;color:var(--gold-light);margin-bottom:6px}
  .spec-card__list{list-style:none;font-size:17px;line-height:1.45;color:var(--white);margin-bottom:16px}
  .spec-card__list:last-child{margin-bottom:0}

  .contact-row{position:absolute;left:70px;bottom:120px;display:flex;flex-direction:column;gap:6px;font-size:16px;color:var(--cream)}
  .cert-row{position:absolute;right:60px;bottom:110px;display:flex;gap:14px}
  .cert{width:38px;height:38px;border:1.5px solid var(--gold-light);border-radius:50%}
  .cert--square{border-radius:4px}
  .barcode-space{position:absolute;left:70px;bottom:160px;width:150px;height:0}

  .about__heading{position:absolute;left:0;right:0;top:60px;text-align:center;font-family:"Playfair Display",Georgia,serif;font-size:52px;color:var(--white)}
  .about__heading .accent{color:var(--gold-light);font-weight:700}
  .about__quote{position:absolute;left:90px;right:90px;top:150px;text-align:center;font-size:21px;font-style:italic;line-height:1.4;color:var(--cream)}
  .lifestyle{position:absolute;left:192px;top:280px;width:300px;height:300px;border-radius:50%;border:5px solid var(--gold);background:radial-gradient(circle at 50% 40%,#d9d2dc,#8d8592 55%,#3d3842)}
  .benefits{position:absolute;left:60px;right:60px;top:630px;display:flex;justify-content:space-between}
  .benefit{width:170px;border:1.5px solid var(--gold);padding:16px 10px;text-align:center}
  .benefit .feature__icon{width:54px;height:54px}
  .benefit__text{font-size:15px;line-height:1.3;color:var(--white)}
  .side-contact{position:absolute;left:0;right:0;bottom:50px;text-align:center;font-size:16px;line-height:1.5;color:var(--cream)}
</style>
</head>
<body>
<main class="sheet">

  <!-- Front panel -->
  <section class="stage">
    <article class="panel panel--face">
      <div class="brand-tab"><span class="brand-tab__name">KRV</span></div>
      <h1 class="title"><span class="title__main">Zenith<br>Max</span><span class="title__sub">Upright<br>Dryer</span></h1>
      <div class="product-visual product-visual--front" role="img" aria-label="Product render of the KRV upright hood dryer on its stand"></div>
      <p class="tagline tagline--front">Effortless Styling.<br>Professional Results.</p>
      <div class="rule" style="left:70px;right:70px;top:672px"></div>
      <ul class="features">
        <li class="feature">
          <div class="feature__icon"><svg width="30" height="30" viewBox="0 0 30 30" fill="none" stroke="#e8cd84" stroke-width="2"><path d="M15 3v24M9 9l6-6 6 6M9 21l6 6 6-6"/></svg></div>
          <p class="feature__label">Adjustable Height</p><p class="feature__note">For all users &amp; settings</p>
        </li>
        <li class="feature">
          <div class="feature__icon"><svg width="30" height="30" viewBox="0 0 30 30" fill="none" stroke="#e8cd84" stroke-width="2"><circle cx="15" cy="15" r="4"/><circle cx="15" cy="15" r="10" stroke-dasharray="3 3"/></svg></div>
          <p class="feature__label">Ionic Technology</p><p class="feature__note">Faster, frizz-free drying</p>
        </li>
        <li class="feature">
          <div class="feature__icon"><svg width="30" height="30" viewBox="0 0 30 30" fill="none" stroke="#e8cd84" stroke-width="2"><path d="M25 15a10 10 0 1 1-3-7"/><path d="M23 3v6h-6"/></svg></div>
          <p class="feature__label">360° Heat Distribution</p><p class="feature__note">Even styling every time</p>
        </li>
        <li class="feature">
          <div class="feature__icon"><svg width="30" height="30" viewBox="0 0 30 30" fill="none" stroke="#e8cd84" stroke-width="2"><path d="M8 12h14l-2 14H10z"/><path d="M11 12a4 4 0 0 1 8 0"/></svg></div>
          <p class="feature__label">Lightweight &amp; Portable</p><p class="feature__note">Easy to move &amp; assemble</p>
        </li>
      </ul>
      <p class="cta cta--front">Elevate Your Look with KRV Professional-Grade Tools.</p>
    </article>
  </section>

  <!-- Back panel -->
  <section class="stage">
    <article class="panel panel--face">
      <div class="brand-tab"><span class="brand-tab__name">KRV</span></div>
      <h2 class="title"><span class="title__main">Zenith<br>Max</span><span class="title__sub">Upright<br>Dryer</span></h2>
      <p class="tagline tagline--back">Effortless Styling.<br>Professional Results.</p>
      <div class="product-visual product-visual--back" role="img" aria-label="Small product image of the upright dryer on its stand"></div>
      <div class="spec-card">
        <h3 class="spec-card__heading">Product Specifications</h3>
        <ul class="spec-card__list"><li>Voltage: 110V-240V</li><li>Adjustable Height Range: X to Y inches</li><li>Dryer Weight: X lbs</li></ul>
        <h3 class="spec-card__heading">What’s Included</h3>
        <ul class="spec-card__list"><li>1 Stand-Up Dryer</li><li>Adjustable Stand</li><li>User Manual</li></ul>
        <h3 class="spec-card__heading">Care Instructions</h3>
        <ul class="spec-card__list"><li>Clean with a damp cloth after use. Store in a cool, dry place.</li></ul>
      </div>
      <p class="cta" style="bottom:220px">Elevate Your Look with KRV Professional-Grade Tools.</p>
      <div class="contact-row"><span>www.KRVhome.com</span><span>care@KRVhome.com</span><span>#KRVRadiance</span></div>
      <div class="cert-row" aria-label="Certification marks">
        <span class="cert"></span><span class="cert cert--square"></span><span class="cert"></span><span class="cert cert--square"></span>
      </div>
    </article>
  </section>

  <!-- Side panel -->
  <section class="stage">
    <article class="panel panel--side">
      <h2 class="about__heading">About <span class="accent">KRV</span></h2>
      <p class="about__quote">“At KRV, we believe beauty is power. Our tools are designed with precision, ensuring every style feels as beautiful as you are.”</p>
      <div class="lifestyle" role="img" aria-label="Lifestyle photo of a stylist using the dryer in a salon"></div>
      <ul class="benefits">
        <li class="benefit">
          <div class="feature__icon"><svg width="26" height="26" viewBox="0 0 30 30" fill="none" stroke="#e8cd84" stroke-width="2"><path d="M6 22h18M6 15h18M6 8h18"/><circle cx="11" cy="22" r="2"/><circle cx="19" cy="15" r="2"/><circle cx="14" cy="8" r="2"/></svg></div>
          <p class="benefit__text">3 Heat Settings for customizable control.</p>
        </li>
        <li class="benefit">
          <div class="feature__icon"><svg width="26" height="26" viewBox="0 0 30 30" fill="none" stroke="#e8cd84" stroke-width="2"><path d="M5 12h5l6-5v16l-6-5H5z"/></svg></div>
          <p class="benefit__text">Quiet operation for a professional salon experience.</p>
        </li>
        <li class="benefit">
          <div class="feature__icon"><svg width="26" height="26" viewBox="0 0 30 30" fill="none" stroke="#e8cd84" stroke-width="2"><rect x="6" y="8" width="18" height="14" rx="2"/><path d="M12 8V5h6v3"/></svg></div>
          <p class="benefit__text">Compact foldable design for storage and travel.</p>
        </li>
      </ul>
      <p class="side-contact">KRV Beauty | www.KRVhome.com<br>Customer Care: care@KRVhome.com</p>
    </article>
  </section>

</main>
</body>
</html>
```